Copper Lantern

Need a business card for our restaurant. Restaurant and Bar in the mountains of North Idaho. Rustic looking card

rustic design, wood and metal looking, primarily neutral colors

• Name, address, phone number, website, email address

```html
<!DOCTYPE html>
<html lang="en">
<head>
<meta charset="utf-8">
<title>Copper Lantern – Business Card</title>
<link href="https://fonts.googleapis.com/css2?family=Montserrat:wght@400;700&display=swap" rel="stylesheet">
<style>
  :root {
    --backdrop: #2a2a2b;
    --card: #161514;
    --grain-dark: #121110;
    --grain-light: #1d1b19;
    --ink: #ffffff;
    --ink-soft: #e4e2de;
    --steel-dark: #3a3a3a;
    --steel-mid: #8d8d8b;
    --steel-light: #d6d5d2;
  }
  * { box-sizing: border-box; margin: 0; padding: 0; }
  html, body { width: 1200px; height: 993px; overflow: hidden; }
  body {
    background: var(--backdrop);
    font-family: "Montserrat", sans-serif;
    color: var(--ink);
    display: flex;
    align-items: center;
    justify-content: center;
    gap: 90px;
  }
  .card {
    width: 340px;
    height: 580px;
    border-radius: 26px;
    position: relative;
    overflow: hidden;
    box-shadow: 0 18px 40px rgba(0,0,0,.55), inset 0 0 0 2px rgba(214,213,210,.18);
    /* dark wood grain */
    background:
      repeating-linear-gradient(92deg,
        rgba(255,255,255,0) 0px, rgba(255,255,255,.025) 2px,
        rgba(0,0,0,0) 5px, rgba(0,0,0,.12) 7px, rgba(255,255,255,0) 11px),
      repeating-linear-gradient(88deg,
        var(--grain-dark) 0px, var(--grain-light) 18px, var(--grain-dark) 34px, #191715 52px, var(--grain-dark) 70px),
      var(--card);
  }
  .card-back__pattern {
    position: absolute;
    inset: 0;
    /* brushed metal sheen over the wood */
    background:
      repeating-linear-gradient(0deg, rgba(255,255,255,.05) 0 1px, rgba(0,0,0,.05) 1px 3px),
      linear-gradient(125deg, rgba(12,12,12,.2) 0%, rgba(28,28,28,.3) 42%, rgba(110,110,108,.85) 60%, rgba(205,204,200,.95) 100%);
  }
  .wordmark {
    display: flex;
    align-items: center;
    gap: 10px;
    font-weight: 700;
    color: var(--ink);
    letter-spacing: .08em;
    text-transform: uppercase;
    white-space: nowrap;
  }
  .wordmark__dot {
    width: 14px; height: 14px;
    border-radius: 50%;
    background: var(--ink);
    flex: none;
  }
  .card-back__wordmark {
    position: absolute;
    left: 50%; top: 50%;
    transform: translate(-50%, -50%);
    background: var(--card);
    padding: 14px 18px;
    border-radius: 40px;
    font-size: 16px;
    box-shadow: 0 0 0 3px var(--steel-light);
  }
  .card-front {
    display: flex;
    flex-direction: column;
    align-items: center;
    padding: 50px 40px 0;
  }
  .metal-plate {
    width: 100%;
    padding: 16px 0;
    border-radius: 10px;
    display: flex;
    justify-content: center;
    background:
      repeating-linear-gradient(0deg, rgba(255,255,255,.06) 0 1px, rgba(0,0,0,.08) 1px 3px),
      linear-gradient(180deg, var(--steel-dark), #232323);
    box-shadow: inset 0 0 0 1.5px rgba(214,213,210,.55), 0 4px 10px rgba(0,0,0,.4);
  }
  .card-front__wordmark { font-size: 19px; }
  .person { text-align: center; margin-top: 58px; }
  .person__name { font-weight: 700; font-size: 26px; }
  .person__role { font-size: 15px; color: var(--ink-soft); margin-top: 4px; font-weight: 400; }
  .divider {
    display: flex; align-items: center; gap: 8px;
    width: 100%; margin: 24px 0 18px;
  }
  .divider::before, .divider::after {
    content: ""; flex: 1; height: 1.5px; background: var(--ink);
  }
  .divider__icons { display: flex; gap: 6px; }
  .icon {
    width: 24px; height: 24px; border-radius: 5px;
    background: var(--ink); display: flex; align-items: center; justify-content: center;
  }
  .contact { text-align: center; font-size: 16px; line-height: 1.55; }
  .rule { width: 100%; height: 1.5px; background: var(--ink); margin: 18px 0; }
  .address { text-align: center; font-size: 16px; line-height: 1.55; }
</style>
</head>
<body>
  <section class="card card-back">
    <div class="card-back__pattern" role="img" aria-label="Repeating pattern of the restaurant emblem fading from black to brushed silver"></div>
    <div class="wordmark card-back__wordmark"><span class="wordmark__dot"></span>Copper Lantern</div>
  </section>

  <section class="card card-front">
    <div class="metal-plate">
      <div class="wordmark card-front__wordmark"><span class="wordmark__dot"></span>Copper Lantern</div>
    </div>

    <div class="person">
      <h1 class="person__name">Owen Hartley</h1>
      <p class="person__role">Managing Director</p>
    </div>

    <div class="divider">
      <div class="divider__icons">
        <span class="icon" aria-label="phone">
          <svg width="14" height="14" viewBox="0 0 24 24"><path fill="#161514" d="M6.6 10.8a15 15 0 0 0 6.6 6.6l2.2-2.2a1 1 0 0 1 1-.25 11.4 11.4 0 0 0 3.6.6 1 1 0 0 1 1 1V20a1 1 0 0 1-1 1A17 17 0 0 1 3 4a1 1 0 0 1 1-1h3.5a1 1 0 0 1 1 1c0 1.25.2 2.45.6 3.6a1 1 0 0 1-.25 1z"/></svg>
        </span>
        <span class="icon" aria-label="email">
          <svg width="14" height="14" viewBox="0 0 24 24"><rect x="2" y="5" width="20" height="14" rx="2" fill="#161514"/><path d="M3 6l9 7 9-7" stroke="#fff" stroke-width="2" fill="none"/></svg>
        </span>
        <span class="icon" aria-label="website">
          <svg width="14" height="14" viewBox="0 0 24 24" fill="none" stroke="#161514" stroke-width="2"><circle cx="12" cy="12" r="9"/><path d="M3 12h18M12 3c3 3 3 15 0 18M12 3c-3 3-3 15 0 18"/></svg>
        </span>
      </div>
    </div>

    <div class="contact">
      <p>123 456 789</p>
      <p>info@yourgmail.com</p>
      <p>www.yourwebsite.com</p>
    </div>

    <div class="rule"></div>

    <div class="address">
      <p>Your address, City</p>
      <p>State, Zip 1234</p>
    </div>
  </section>
</body>
</html>
```